Brisbane IT support business needs our first website

Hi All,

We are after a new website design for our IT solutions and support business.The business name is Harbourline Computing Services Group, or HCSG for short. We provide a range of solutions and services within the IT space.

I would like to utilize the two colours in our business logo I have uploaded.

I understand this is initially for the design only aspect of the site, but I would like to engage the winner to finish coding the website and finalize after also.

Target Market(s)

Other businesses owners and home users.

Industry/Entity Type

Business

Requirements
Must have
• Nice clean and functional design utilizing our business colours from the logo.

```html
<!DOCTYPE html>
<html lang="en">
<head>
<meta charset="utf-8">
<title>Harbourline Computing Services Group</title>
<link href="https://fonts.googleapis.com/css2?family=Figtree:wght@500;600;700&family=Lato:ital,wght@0,300;0,400;0,700;0,900;1,400;1,700&display=swap" rel="stylesheet">
<style>
:root{
  --orange:#ee7f27;
  --navy:#0b4a63;
  --card:rgba(52,118,142,.78);
  --text:#333;
  --muted:#666;
  --quote-bg:#f2f2f2;
  --foot:#262626;
  --foot-mid:#333;
  --foot-base:#111;
}
*{margin:0;padding:0;box-sizing:border-box}
html,body{width:1200px;height:1108px;overflow:hidden;background:#fff}
body{position:relative;font-family:Lato,sans-serif;color:var(--text)}
.abs{position:absolute}

/* header */
.site-header{position:absolute;left:0;top:0;width:1200px;height:123px;background:#fff}
.brand{left:131px;top:14px;display:flex;align-items:center;gap:14px}
.brand-dot{width:84px;height:84px;border-radius:50%;background:var(--navy)}
.brand-name{font-family:Figtree,sans-serif;font-weight:700;font-size:46px;color:var(--orange);letter-spacing:1px}
.contact-bar{right:131px;top:18px;display:flex;align-items:center;gap:18px;font-family:Figtree,sans-serif;color:var(--navy);white-space:nowrap}
.contact-item{display:flex;align-items:center;gap:10px}
.contact-item .ico{width:34px;height:34px;flex:none}
.contact-email{font-size:14px;font-weight:600}
.contact-phone{font-size:19px;font-weight:600}
.main-nav{right:131px;top:82px;display:flex;align-items:center;font-family:Figtree,sans-serif;font-weight:600;font-size:14px;letter-spacing:.3px;color:#333}
.main-nav span{padding:0 15px;border-left:1px solid #ccc;line-height:12px}
.main-nav span:first-child{border-left:0}
.main-nav span:last-child{padding-right:0}
.main-nav .active{color:var(--orange);position:relative}
.main-nav .active::after{content:"";position:absolute;left:18px;right:14px;top:20px;height:3px;background:var(--orange)}

/* hero */
.hero{position:absolute;left:0;top:123px;width:1200px;height:515px}
.hero-photo{position:absolute;inset:0;background:radial-gradient(ellipse at 65% 45%,#2f6a83 0%,#1d5269 45%,#0d3346 100%)}
.hero-title{position:absolute;left:0;width:1200px;text-align:center;font-weight:300;color:#fff}
.hero-title.l1{top:64px;font-size:56px;color:var(--orange)}
.hero-title.l1 b{font-weight:900}
.hero-title.l2{top:130px;font-size:46px}
.hero-rule{position:absolute;left:461px;top:199px;width:278px;height:1px;background:rgba(255,255,255,.55)}
.feature{position:absolute;top:274px;width:169px;height:178px;background:var(--card);border-radius:3px;text-align:center;color:#fff;font-family:Figtree,sans-serif;font-weight:600;font-size:19px;line-height:25px}
.feature .badge{width:80px;height:80px;border-radius:50%;background:var(--orange);margin:18px auto 16px;display:flex;align-items:center;justify-content:center}
.hero-arrow{position:absolute;top:338px}

/* review */
.review-title{left:0;top:678px;width:1200px;text-align:center;font-family:Figtree,sans-serif;font-weight:600;font-size:27px;color:var(--navy)}
.review-sub{left:0;top:713px;width:1200px;text-align:center;font-size:15px;color:var(--muted)}
.review-divider{left:356px;top:740px}
.quote-box{left:131px;top:775px;width:800px;height:98px;background:var(--quote-bg)}
.quote-text{left:149px;top:788px;width:752px;font-style:italic;font-size:13.6px;line-height:24px;color:#333}
.quote-text::before{content:"\201C";font-family:Georgia,serif;font-size:44px;color:#aaa;font-style:normal;vertical-align:-22px;margin-right:6px;line-height:0}
.avatar-ring{left:931px;top:767px;width:120px;height:120px;border-radius:50%;background:#e9e9e9;border:4px solid #fff;box-shadow:0 0 0 2px #ddd}
.avatar{position:absolute;inset:4px;border-radius:50%;background:linear-gradient(160deg,#d7e6f0,#9fb7c6)}
.quote-name{right:266px;top:893px;font-style:italic;font-weight:700;font-size:13px;color:#333}

/* footer */
.site-footer{left:0;top:940px;width:1200px;height:103px;background:var(--foot);color:#fff}
.foot-social-panel{position:absolute;left:502px;top:0;width:196px;height:103px;background:var(--foot-mid)}
.foot-head{position:absolute;font-weight:700;font-size:15px}
.news-form{position:absolute;left:197px;top:48px;display:flex}
.news-input{width:170px;height:27px;background:#fff;color:#555;font-style:italic;font-size:11px;padding:7px 11px}
.news-btn{height:27px;background:var(--orange);color:#fff;font-weight:700;font-size:13px;padding:6px 11px;letter-spacing:.3px}
.social{position:absolute;left:530px;top:47px;display:flex;gap:9px}
.social span{width:29px;height:29px;border-radius:50%;background:#fff}
.foot-info{position:absolute;font-size:13.5px;line-height:18px;white-space:nowrap}
.site-base{left:0;top:1043px;width:1200px;height:65px;background:var(--foot-base);color:#ddd;font-size:13.5px;text-align:center;line-height:65px}
</style>
</head>
<body>

<header class="site-header">
  <div class="abs brand"><span class="brand-dot"></span><span class="brand-name">HCSG</span></div>

  <div class="abs contact-bar">
    <div class="contact-item contact-email">
      <svg class="ico" viewBox="0 0 34 34"><path d="M2 2h24l6 15-6 15H2z" fill="none" stroke="#ee7f27" stroke-width="2"/><rect x="7" y="11" width="15" height="12" fill="#ee7f27"/><path d="M7 11l7.5 6 7.5-6" fill="none" stroke="#fff" stroke-width="1.5"/></svg>
      <span>hello@harbourline.example</span>
    </div>
    <div class="contact-item contact-phone">
      <svg class="ico" viewBox="0 0 34 34"><path d="M2 2h24l6 15-6 15H2z" fill="none" stroke="#ee7f27" stroke-width="2"/><rect x="10" y="8" width="10" height="18" rx="2" fill="#ee7f27"/><rect x="12" y="11" width="6" height="7" fill="#fff"/></svg>
      <span>555-014-2290</span>
    </div>
  </div>

  <nav class="abs main-nav">
    <span class="active">HOME</span><span>ABOUT</span><span>SERVICES</span><span>TECHNOLOGY</span><span>SOLUTIONS</span><span>SUPPORT</span><span>CONTACT</span>
  </nav>
</header>

<section class="hero">
  <div class="hero-photo" role="img" aria-label="Blurred photo of a laptop on a desk with floating app icons and a chart, tinted dark teal"></div>
  <h1 class="hero-title l1"><b>Success</b> With</h1>
  <div class="hero-title l2">Our Creative Solutions</div>
  <div class="hero-rule"></div>

  <svg class="hero-arrow" style="left:131px" width="26" height="50" viewBox="0 0 26 50"><path d="M24 2L2 25l22 23" fill="none" stroke="rgba(255,255,255,.6)" stroke-width="2"/></svg>
  <svg class="hero-arrow" style="left:1043px" width="26" height="50" viewBox="0 0 26 50"><path d="M2 2l22 23L2 48" fill="none" stroke="rgba(255,255,255,.6)" stroke-width="2"/></svg>

  <div class="feature" style="left:187px">
    <div class="badge"><svg width="46" height="46" viewBox="0 0 46 46"><path d="M30 4a11 11 0 0 0-10 15L5 34a4 4 0 0 0 6 6l15-15A11 11 0 0 0 41 15l-6 6-6-2-2-6 6-6a11 11 0 0 0-3-3z" fill="#fff"/><circle cx="9" cy="37" r="2" fill="#ee7f27"/></svg></div>
    IT<br>Support
  </div>
  <div class="feature" style="left:403px">
    <div class="badge"><svg width="44" height="48" viewBox="0 0 44 48"><ellipse cx="22" cy="7" rx="20" ry="6" fill="#fff"/><path d="M2 12c0 4 9 7 20 7s20-3 20-7v8c0 4-9 7-20 7S2 24 2 20z" fill="#fff"/><path d="M2 25c0 4 9 7 20 7s20-3 20-7v8c0 4-9 7-20 7S2 37 2 33z" fill="#fff"/><path d="M2 38c0 4 9 7 20 7s20-3 20-7v3c0 4-9 7-20 7S2 45 2 41z" fill="#fff"/></svg></div>
    Data<br>Management
  </div>
  <div class="feature" style="left:628px">
    <div class="badge"><svg width="52" height="40" viewBox="0 0 52 40"><path d="M2 8l10-4 8 4 8-3 12 2 10 4-4 14-8 8-6 4-4-2-4 2-4-3-4 1-4-4-4 0-4-6L0 22z" fill="#fff"/><path d="M14 20l6 6M19 18l7 7M24 16l7 7M20 10l8 6" stroke="#ee7f27" stroke-width="2" fill="none"/></svg></div>
    Customer<br>Relationship
  </div>
  <div class="feature" style="left:844px">
    <div class="badge"><svg width="38" height="44" viewBox="0 0 38 44"><path d="M9 20v-7a10 10 0 0 1 20 0v7" fill="none" stroke="#fff" stroke-width="5"/><rect x="3" y="19" width="32" height="24" rx="3" fill="#fff"/></svg></div>
    100%<br>Secure
  </div>
</section>

<section>
  <h2 class="abs review-title">Our Customer Review</h2>
  <p class="abs review-sub">Lorem ipsum dolor sit amet, consectetur Donec a consequat mag&nbsp; Aenean eu velit&nbsp; Aenean sollicitudin</p>
  <svg class="abs review-divider" width="488" height="18" viewBox="0 0 488 18">
    <line x1="0" y1="9" x2="214" y2="9" stroke="#cfcfcf"/><line x1="274" y1="9" x2="488" y2="9" stroke="#cfcfcf"/>
    <g fill="#c8c8c8">
      <path d="M226 2l2.2 4.6 5 .6-3.7 3.4 1 5-4.5-2.5-4.5 2.5 1-5-3.7-3.4 5-.6z"/>
      <path d="M244 2l2.2 4.6 5 .6-3.7 3.4 1 5-4.5-2.5-4.5 2.5 1-5-3.7-3.4 5-.6z"/>
      <path d="M262 2l2.2 4.6 5 .6-3.7 3.4 1 5-4.5-2.5-4.5 2.5 1-5-3.7-3.4 5-.6z"/>
    </g>
  </svg>
  <div class="abs quote-box"></div>
  <svg class="abs" style="left:838px;top:775px" width="90" height="114" viewBox="0 0 90 114"><path d="M0 0h62l28 26v72H32l-12 16-12-16H0z" fill="#f2f2f2"/></svg>
  <p class="abs quote-text">Lorem sum dolor sit amet, consectetuer adipiscing elit, sed diam nonummy nibh euismod tincidunt ut laoreet re agn aliqam erat volutpat wisi enim ad minim veniam, quis nostrud exerci tation ullamcorper suscipit lobortis nisl ut aliquip modo conseuatis autem vel eum iriure dolor in hendrerit in vulputate velit esse molestie consequat, vel illum dolore eu.</p>
  <div class="abs avatar-ring"><div class="avatar" role="img" aria-label="Portrait photo of the reviewing customer"></div></div>
  <p class="abs quote-name">Marcus Ellory, Northgate Ltd , USA</p>
</section>

<footer class="abs site-footer">
  <svg class="abs" style="left:131px;top:24px" width="50" height="48" viewBox="0 0 50 48"><path d="M2 18L25 2l23 16v28H2z" fill="#fff"/><path d="M9 7h32v18L25 35 9 25z" fill="#262626"/><path d="M2 18l23 16 23-16" fill="none" stroke="#262626" stroke-width="2"/><path d="M2 46l18-14M48 46L30 32" stroke="#262626" stroke-width="2"/></svg>
  <div class="foot-head" style="left:198px;top:20px">Sign up for Newsletter</div>
  <div class="news-form"><div class="news-input">Your Email Address</div><div class="news-btn">SUBSCRIBE</div></div>

  <div class="foot-social-panel"></div>
  <div class="foot-head" style="left:530px;top:20px">Follow us on</div>
  <div class="social" aria-label="Social profiles"><span></span><span></span><span></span><span></span></div>

  <svg class="abs" style="left:734px;top:22px" width="12" height="16" viewBox="0 0 12 16"><path d="M6 0a6 6 0 0 1 6 6c0 4-6 10-6 10S0 10 0 6a6 6 0 0 1 6-6z" fill="#fff"/><circle cx="6" cy="6" r="2.3" fill="#262626"/></svg>
  <div class="foot-info" style="left:756px;top:20px">123&nbsp; Lorem Sum Dolor<br>Sit Amet Consectuer<br>Adipiscing Elit</div>
  <svg class="abs" style="left:918px;top:22px" width="10" height="16" viewBox="0 0 10 16"><rect x="0" y="0" width="10" height="16" rx="2" fill="#fff"/><rect x="2" y="2" width="6" height="9" fill="#262626"/></svg>
  <div class="foot-info" style="left:948px;top:20px;font-weight:700">(555) 014-2290</div>
  <svg class="abs" style="left:916px;top:59px" width="14" height="10" viewBox="0 0 14 10"><rect width="14" height="10" fill="#fff"/><path d="M0 0l7 6 7-6" fill="none" stroke="#262626" stroke-width="1.3"/></svg>
  <div class="foot-info" style="left:948px;top:55px">info@harbourline.example</div>
</footer>

<div class="abs site-base">© 2014 Harbourline Computing Services Group. All Rights Reserved.</div>

</body>
</html>
```